Brintel Works - Fast, Efficient and Gas Mainteance for Domestic, Commercial and Industrial clients

We are in the process of purchasing a new business and would like to get a new logo and business card.
Business is a gas maintenance business that also does new gas installations.
Has been established since 1988.
Services include:
Install all types of gas appliances & equipment inc. hot water units
Maintain / repair / replace all types of gas appliances & equipment

Target Market(s)

Domestic, Commercial and Industrial clients

Industry/Entity Type

Business

Contact Information for Business Card

admin@brintelworks.com.au
07 3918 4726
Brintel Works PTY LTD

Logo Text

Gas Fitting & Plumbing Maintenance Specialists

Font styles to use
Sans Serif

Requirements
Must have
• Logo
• Business name, contact number, email address, web address
• Domestic | Commercial | Industrial Est Since 1988
Nice to have
• Possibly a black card with a flame logo to one side
Should not have
• Spelling errors

```html
<!DOCTYPE html>
<html lang="en">
<head>
<meta charset="utf-8">
<title>Brintel Works – Business Card</title>
<link rel="stylesheet" href="https://fonts.googleapis.com/css2?family=Varela+Round&family=Noto+Sans:wght@400&display=swap">
<style>
  :root {
    --backdrop: #ece7df;
    --card-dark: #1f1f20;
    --card-orange: #f28731;
    --brand-orange: #f28a30;
    --tagline-yellow: #e6d321;
    --ink-dark: #1d1a17;
    --white: #ffffff;
  }
  * { margin: 0; padding: 0; box-sizing: border-box; }
  html, body {
    width: 1200px;
    height: 569px;
    overflow: hidden;
    background: var(--backdrop);
  }
  .canvas {
    position: relative;
    width: 1200px;
    height: 569px;
  }
  .card {
    position: absolute;
    top: 166px;
    width: 402px;
    height: 236px;
    border-radius: 10px;
  }
  .card--front {
    left: 175px;
    background: var(--card-dark);
  }
  .card--back {
    left: 624px;
    background: var(--card-orange);
  }
  .brand {
    position: absolute;
    left: 0;
    right: 0;
    top: 104px;
    display: flex;
    align-items: center;
    justify-content: center;
    gap: 10px;
  }
  .brand__dot {
    width: 18px;
    height: 18px;
    border-radius: 50%;
    background: var(--brand-orange);
  }
  .brand__name {
    font-family: "Varela Round", sans-serif;
    font-size: 30px;
    line-height: 1;
    color: var(--brand-orange);
  }
  .tagline {
    position: absolute;
    left: 0;
    right: 0;
    top: 197px;
    text-align: center;
    font-family: "Noto Sans", sans-serif;
    font-size: 9.5px;
    color: var(--tagline-yellow);
  }
  .back-name {
    position: absolute;
    left: 0;
    right: 0;
    top: 103px;
    text-align: center;
    font-family: "Varela Round", sans-serif;
    font-size: 24px;
    line-height: 1;
    color: var(--white);
  }
  .contact {
    position: absolute;
    left: 0;
    right: 0;
    top: 162px;
    text-align: center;
    font-family: "Noto Sans", sans-serif;
    font-size: 11.5px;
    line-height: 16.5px;
    color: var(--ink-dark);
    list-style: none;
  }
</style>
</head>
<body>
  <main class="canvas">
    <section class="card card--front" aria-label="Card front">
      <div class="brand">
        <span class="brand__dot"></span>
        <span class="brand__name">Brintel Works</span>
      </div>
      <p class="tagline">• Domestic • Commercial • Industrial Est Since 1988</p>
    </section>

    <section class="card card--back" aria-label="Card back">
      <p class="back-name">Brintel Works</p>
      <ul class="contact">
        <li>admin@brintelworks.com.au</li>
        <li>07 3918 4726</li>
        <li>Brintel Works PTY LTD</li>
      </ul>
    </section>
  </main>
</body>
</html>
```